Roofing web site brvt roofing

Look at some of our competitors web page we like something similar with NYC roofing
https://www.quillbarroofing.example/
Maybe a skyline picture of nyc at the home page with a picture of flat roofing installation

Target Market(s)

Commercial and residential flat roofs

Industry/Entity Type

Flat Roofing industry

Coding

Coded - Design and coding required

Number of Pages Required

2 page

Font styles to use
Decorative
Script

Colors

Designer to choose colors to be used in the design.

Requirements
Must have
• At BRVT Roofing, we are a trusted and reputable roofing company specializing in new construction flat roof installation and repair. With years of experience in the industry, we take pride in providing exceptional roofing solutions to our valued clients. Our team of highly skilled and dedicated roofing professionals understands the unique challenges and requirements of new construction projects. We work closely with builders, contractors, and architects to design and install flat roofs that meet the specific needs of each project. From commercial buildings to residential complexes, we have the expertise to deliver reliable and durable roofing solutions. When it comes to flat roof repairs, we are your go-to experts. Our experienced technicians conduct thorough inspections to identify the root cause of any issues your roof may be experiencing. We utilize the latest industry techniques and high-quality materials to efficiently repair your flat roof, ensuring its integrity and longevity. At BRVT Roofing, we prioritize customer satisfaction above all else. We believe in building strong relationships with our clients by providing exceptional craftsmanship and outstanding customer service. Our team is dedicated to delivering projects on time, within budget, and to the highest standards of quality. We understand that a well-maintained roof is essential for protecting your property and ensuring the safety of its occupants. That's why we use only the best materials and employ skilled professionals who are trained in the latest roofing practices. Our commitment to excellence is evident in every project we undertake. As a fully licensed and insured roofing company, we prioritize safety and adhere to industry regulations and best practices. We take every precaution to create a safe working environment for our team and minimize any disruptions to your daily routine. When you choose BRVT Roofing, you can trust that you are working with a reliable and reputable company that will deliver exceptional results. We are committed to exceeding your expectations and providing you with a roof that is built to last. Contact us today for all your new construction flat roof installation and repair needs.
Nice to have
• NYC skyline background with commercial roofing pictures of torching roofing

```html
<!DOCTYPE html>
<html lang="en">
<head>
<meta charset="utf-8">
<title>Brevett NY Roofing – Expert Flat Roof Services</title>
<link href="https://fonts.googleapis.com/css2?family=Poppins:wght@600;700;800&family=Figtree:wght@400;500;600&display=swap" rel="stylesheet">
<style>
:root{
  --blue:#0a6ebd;
  --orange:#f0541e;
  --ink:#111;
  --text:#444;
  --paper:#fff;
  --mist:#f1f0ef;
  --footer:#171717;
  --footer-text:#f2f2f2;
}
*{box-sizing:border-box;margin:0;padding:0}
html,body{width:1200px;height:4228px;overflow:hidden}
body{font-family:"Figtree",sans-serif;color:var(--text);background:var(--paper);position:relative}
.abs{position:absolute}
.heading{font-family:"Poppins",sans-serif;font-weight:800;color:var(--ink);text-transform:uppercase}
.rule{position:absolute;height:4px;width:52px;background:var(--blue)}
.btn{position:absolute;background:var(--orange);color:#fff;font-family:"Poppins",sans-serif;font-weight:700;font-size:15px;display:flex;align-items:center;justify-content:center;text-transform:uppercase}
.photo{position:absolute}

/* header */
.phone-btn{left:130px;top:28px;width:218px;height:54px;border:2px solid var(--blue);display:flex;align-items:center;justify-content:center;gap:12px;color:var(--blue);font-family:"Poppins",sans-serif;font-weight:700;font-size:19px}
.brand{position:absolute;display:flex;align-items:center;gap:10px;font-family:"Poppins",sans-serif;font-weight:600;white-space:nowrap}
.brand-mark{width:14px;height:14px;background:currentColor;flex:none}
.brand-top{left:500px;top:46px;font-size:20px;color:#333}
.tool{position:absolute;top:36px;width:42px;height:42px;border:2px solid var(--blue);display:flex;align-items:center;justify-content:center}
.nav{left:0;top:125px;width:1200px;height:46px;background:var(--blue);display:flex;justify-content:center}
.nav a{color:#fff;text-decoration:none;font-size:15px;font-weight:500;display:flex;align-items:center;padding:0 28px;height:46px}
.nav a.active{background:var(--orange);margin-right:6px;padding:0 14px}

/* hero */
.hero-photo{left:0;top:171px;width:1200px;height:629px;background:linear-gradient(180deg,#9dbbd6 0%,#d3c2a4 36%,#8e8a83 52%,#a9a9a7 70%,#c4c4c2 100%)}
.hero-title{left:0;top:202px;width:1200px;text-align:center;font-family:"Poppins",sans-serif;font-weight:800;font-size:46px;color:#fff;text-shadow:0 2px 6px rgba(0,0,0,.35)}
.hero-sub{left:0;top:264px;width:1200px;text-align:center;font-family:"Poppins",sans-serif;font-weight:700;font-size:28px;color:rgba(255,255,255,.92);text-shadow:0 2px 6px rgba(0,0,0,.35)}

/* features */
.features{left:0;top:800px;width:1200px;height:288px;background:var(--blue)}
.feature{position:absolute;top:840px;width:300px;color:#fff}
.feature-icon{height:72px;display:flex;align-items:flex-end}
.feature h3{margin-top:22px;font-family:"Poppins",sans-serif;font-weight:700;font-size:18px}
.feature p{margin-top:12px;font-size:13px;line-height:19px;width:215px;opacity:.92}
.vline{position:absolute;top:826px;width:1px;height:230px;background:rgba(255,255,255,.6)}

/* welcome */
.welcome{left:0;top:1088px;width:1200px;height:492px;background:var(--mist)}
.welcome-photo{left:580px;top:1088px;width:620px;height:492px;background:linear-gradient(90deg,var(--mist) 0%,#d6d8da 18%,#a9b2ba 45%,#7c858e 75%,#6a7079 100%)}
.welcome-title{left:133px;top:1128px;font-size:33px;line-height:48px}
.welcome-copy{left:133px;top:1281px;width:480px;font-size:16px;line-height:24px}

/* services */
.section-title{left:0;width:1200px;text-align:center;font-size:32px}
.card-photo{top:1727px;width:295px;height:224px}
.card{position:absolute;top:1951px;width:266px;height:296px;border:2px solid var(--blue);border-top:none;text-align:center;padding:30px 14px 0}
.card h3{font-family:"Poppins",sans-serif;font-weight:600;font-size:19px;color:var(--ink)}
.card p{margin-top:14px;font-size:13px;line-height:19.5px}
.card .btn{position:relative;margin:20px auto 0;width:112px;height:36px;font-size:13px}

/* why */
.why-photo{left:0;top:2310px;width:1200px;height:552px;background:linear-gradient(100deg,#5a5c5f 0%,#55575a 50%,#3c3e42 75%,#2b2c2e 100%)}
.why-title{left:133px;top:2364px;color:#fff;font-size:32px}
.badge{position:absolute;width:280px;height:91px;border:2px solid rgba(255,255,255,.85);display:flex;align-items:center;gap:18px;padding-left:22px;color:#fff;font-size:17px;line-height:22px}
.badge-icon{width:46px;height:46px;border-radius:50%;background:#fff;flex:none;display:flex;align-items:center;justify-content:center}
.badge-plain{width:46px;height:46px;background:#fff;flex:none}

/* gallery */
.gallery-photo{top:3016px;width:383px;height:369px}
.arrow{position:absolute;top:3176px;width:46px;height:50px;background:#fff;display:flex;align-items:center;justify-content:center}

/* cta */
.cta-photo{left:0;top:3512px;width:1200px;height:358px;background:linear-gradient(180deg,#0b72c6 0%,#1f86d6 60%,#3b89c0 100%)}
.cta-title{left:0;width:1200px;text-align:center;font-family:"Poppins",sans-serif;font-weight:800;font-size:33px;color:#fff}
.cta-copy{left:0;top:3686px;width:1200px;text-align:center;color:#fff;font-size:18px}
.signup{left:254px;top:3744px;width:691px;height:58px;background:#fff;display:flex;align-items:center;padding-left:24px;gap:16px;font-size:16px;color:#555}

/* footer */
.footer{left:0;top:3870px;width:1200px;height:358px;background:var(--footer);color:var(--footer-text)}
.brand-foot{left:132px;top:3998px;font-size:22px;color:var(--footer-text)}
.fhead{position:absolute;top:3918px;font-family:"Poppins",sans-serif;font-weight:700;font-size:13px;padding-bottom:10px;border-bottom:2px solid #ddd;color:var(--footer-text)}
.fitem{position:absolute;display:flex;gap:12px;align-items:center;font-size:12px;line-height:15px;color:var(--footer-text)}
.fitem .ic{width:22px;height:22px;border-radius:50%;background:#fff;flex:none;display:flex;align-items:center;justify-content:center}
.fmenu{position:absolute;left:748px;top:3960px;font-size:12px;line-height:19.5px;color:var(--footer-text)}
.fline{position:absolute;left:130px;top:4155px;width:935px;height:1px;background:#888}
.copy{position:absolute;left:0;top:4185px;width:1200px;text-align:center;font-size:11px;color:var(--footer-text)}
</style>
</head>
<body>

<!-- header -->
<div class="abs phone-btn">
  <svg width="24" height="24" viewBox="0 0 24 24" fill="none" stroke="currentColor" stroke-width="1.8"><path d="M5 3h4l2 5-2.5 1.5a11 11 0 0 0 6 6L16 13l5 2v4a2 2 0 0 1-2 2A17 17 0 0 1 3 5a2 2 0 0 1 2-2z"/></svg>
  555-014-2290
</div>
<div class="brand brand-top"><span class="brand-mark"></span>Brevett NY Roofing</div>
<div class="tool" style="left:913px"><svg width="20" height="20" viewBox="0 0 24 24" fill="none" stroke="#0a6ebd" stroke-width="2"><circle cx="10" cy="10" r="7"/><path d="M15 15l6 6"/></svg></div>
<div class="tool" style="left:970px"><svg width="22" height="22" viewBox="0 0 24 24" fill="none" stroke="#0a6ebd" stroke-width="2"><path d="M2 3h3l3 12h11l2-8H6"/><circle cx="9" cy="20" r="1.5"/><circle cx="18" cy="20" r="1.5"/></svg></div>
<div class="tool" style="left:1027px"><svg width="20" height="20" viewBox="0 0 24 24" fill="none" stroke="#0a6ebd" stroke-width="2"><circle cx="12" cy="8" r="5"/><path d="M3 22c1-5 5-8 9-8s8 3 9 8"/></svg></div>

<nav class="abs nav">
  <a class="active">HOME</a><a>ABOUT US</a><a>SERVICES</a><a>PHOTO GALLERY</a><a>CONTACT US</a>
</nav>

<!-- hero -->
<div class="photo hero-photo" role="img" aria-label="Two roofers torching down flat roofing rolls on a rooftop with the New York City skyline behind"></div>
<h1 class="abs hero-title">EXPERT FLAT ROOF SERVICES</h1>
<p class="abs hero-sub">PROS IN ALL ASPECTS OF ROOFING</p>
<div class="btn" style="left:520px;top:336px;width:160px;height:47px">GET A QUOTE</div>

<!-- features -->
<div class="abs features"></div>
<div class="vline" style="left:405px"></div>
<div class="vline" style="left:752px"></div>
<div class="feature" style="left:135px">
  <div class="feature-icon"><svg width="74" height="72" viewBox="0 0 74 72" fill="#fff"><path d="M28 2C18 20 6 34 6 46a22 22 0 0 0 44 0C50 34 38 20 28 2z"/><path d="M63 50c-4 7-7 11-7 14a7 7 0 0 0 14 0c0-3-3-7-7-14z"/><path d="M16 44a12 12 0 0 0 8 14" stroke="#0a6ebd" stroke-width="4" fill="none"/></svg></div>
  <h3>ROOF LEAK REPAIRS</h3>
  <p>Flat roofing maintenance incudes drainig water, repairing your roof;s infitration system and gerrin rid of debris.</p>
</div>
<div class="feature" style="left:478px">
  <div class="feature-icon"><svg width="60" height="74" viewBox="0 0 60 74" fill="#fff"><path d="M10 22a20 20 0 0 1 40 0h4v6H6v-6z"/><rect x="15" y="31" width="30" height="16" rx="8"/><path d="M2 74c0-14 10-22 28-22s28 8 28 22z"/><rect x="20" y="56" width="20" height="18" fill="#0a6ebd"/></svg></div>
  <h3>FLASHING SERVICES</h3>
  <p>Roof flashing polays an important role in leak prevention at the most vulnerable areas of your roof.</p>
</div>
<div class="feature" style="left:815px">
  <div class="feature-icon"><svg width="64" height="64" viewBox="0 0 64 64" fill="#fff"><rect x="0" y="0" width="38" height="64"/><rect x="40" y="26" width="24" height="38"/><g fill="#0a6ebd"><rect x="8" y="10" width="6" height="8"/><rect x="22" y="10" width="6" height="8"/><rect x="8" y="28" width="6" height="8"/><rect x="22" y="28" width="6" height="8"/><rect x="8" y="46" width="6" height="8"/><rect x="22" y="46" width="6" height="8"/><rect x="48" y="36" width="8" height="6"/><rect x="48" y="50" width="8" height="6"/></g></svg></div>
  <h3>WATERPROOFING EXPERTS</h3>
  <p>Our highly-skilled techiniasn will expertly diagonse your problem areas nad provide you solution to oyur specific need.</p>
</div>

<!-- welcome -->
<div class="abs welcome"></div>
<div class="photo welcome-photo" role="img" aria-label="Roofer in a yellow hard hat kneeling to lay a flat roofing membrane"></div>
<h2 class="abs heading welcome-title">Welcome to<br>Brevett NY Roofing</h2>
<div class="rule" style="left:133px;top:1241px"></div>
<p class="abs welcome-copy">At BRVT Roofing, we are a trusted and reputable roofing company specializing in new construction flat roof installation and repair. With years of experience in the industry, we take pride in providing exceptional roofing solutions to our valued clients. Our team of highly skilled and dedicated roofing professionals understands the unique challenges and requirements of new construction projects.</p>
<div class="btn" style="left:135px;top:1480px;width:127px;height:46px;font-size:14px">READ MORE</div>

<!-- services -->
<h2 class="abs heading section-title" style="top:1622px">Our Services</h2>
<div class="rule" style="left:574px;top:1686px"></div>

<div class="photo card-photo" style="left:131px;background:linear-gradient(180deg,#8b8f94,#2c4e7c 55%,#1e3558)" role="img" aria-label="Roofer unrolling and torching a membrane on a blue flat roof"></div>
<div class="card" style="left:145px">
  <h3>Perfect Installs</h3>
  <p>Your roof is your main defense against the elements. Let us walk you through the best options to fit your needs and once you feel comfortable with your choice, we'll handle the complete installation.</p>
  <div class="btn">READ MORE</div>
</div>

<div class="photo card-photo" style="left:452px;background:linear-gradient(160deg,#b8453a 0%,#d9c8bf 40%,#a8c4b6 70%,#8d8a86)" role="img" aria-label="Worker fitting flashing around a roof skylight"></div>
<div class="card" style="left:466px">
  <h3>Reliable Upgrades</h3>
  <p>If you're looking to update or upgrade your roofing and gutters, we've got you covered. Book a free consultation to discuss our different types of roofing composition and environmentally friendly options!</p>
  <div class="btn">READ MORE</div>
</div>

<div class="photo card-photo" style="left:774px;background:linear-gradient(180deg,#3f5f86,#2e4a6e 50%,#1f2f44)" role="img" aria-label="Gloved hands rolling out a black roofing membrane"></div>
<div class="card" style="left:788px">
  <h3>Upkeep &amp; Repair</h3>
  <p>Age and environmental factors can wreak havoc on your roof. Ignoring problems for too long can cause headaches down the road. Start with a free inspection today!</p>
  <div class="btn">READ MORE</div>
</div>

<!-- why choose -->
<div class="photo why-photo" role="img" aria-label="Close-up of a roofing roll being torched onto a flat roof"></div>
<h2 class="abs heading why-title">Why Choose Brevett Construction?</h2>
<div class="rule" style="left:133px;top:2426px;background:#fff"></div>

<div class="badge" style="left:136px;top:2473px"><span class="badge-icon"><svg width="24" height="24" viewBox="0 0 24 24" fill="none" stroke="#f0541e" stroke-width="2"><rect x="5" y="3" width="14" height="18" rx="2"/><path d="M9 9h6M9 13h6M9 17h3"/></svg></span>Licensed, Bonded,<br>&amp; Insured</div>
<div class="badge" style="left:432px;top:2473px"><span class="badge-icon"><svg width="24" height="24" viewBox="0 0 24 24" fill="none" stroke="#f0541e" stroke-width="2"><circle cx="12" cy="8" r="4"/><path d="M4 21c1-5 4-7 8-7s7 2 8 7"/></svg></span>Reliable &amp; Experienced<br>professionals</div>
<div class="badge" style="left:136px;top:2584px"><span class="badge-icon"><svg width="24" height="24" viewBox="0 0 24 24" fill="none" stroke="#f0541e" stroke-width="2"><rect x="5" y="3" width="14" height="18" rx="2"/><path d="M8 7h8M8 11h2M12 11h2M8 15h2M12 15h2"/></svg></span>Free Evaluations &amp;<br>Estimates</div>
<div class="badge" style="left:432px;top:2584px"><span class="badge-icon"><svg width="24" height="24" viewBox="0 0 24 24" fill="none" stroke="#f0541e" stroke-width="2"><circle cx="12" cy="12" r="9"/><path d="M8 12l3 3 5-6"/></svg></span>Lead-Safe<br>Certified</div>
<div class="badge" style="left:136px;top:2697px"><span class="badge-icon"><svg width="24" height="24" viewBox="0 0 24 24" fill="none" stroke="#f0541e" stroke-width="2"><circle cx="12" cy="12" r="9"/><path d="M12 7v5l3 2"/></svg></span>24/7 Emergency<br>Response</div>
<div class="badge" style="left:432px;top:2697px"><span class="badge-plain"></span>Trade Bureau Accredited<br>Business</div>

<!-- gallery -->
<h2 class="abs heading section-title" style="top:2908px">Photo Gallery</h2>
<div class="rule" style="left:574px;top:2973px"></div>
<div class="photo gallery-photo" style="left:13px;background:linear-gradient(180deg,#e6e6e4,#4c6a58 45%,#55534f)" role="img" aria-label="Roofer in green work trousers torching a roofing roll"></div>
<div class="photo gallery-photo" style="left:410px;background:linear-gradient(180deg,#b9d6ee,#7e9fbb 35%,#38485e 55%,#1f2d44)" role="img" aria-label="Finished dark flat roof under a clear sky"></div>
<div class="photo gallery-photo" style="left:806px;background:linear-gradient(160deg,#d0683a,#b8502a 50%,#8e3c22)" role="img" aria-label="Worker pressure washing an orange tile roof with skylights"></div>
<div class="arrow" style="left:13px"><svg width="16" height="26" viewBox="0 0 16 26" fill="none" stroke="#222" stroke-width="2"><path d="M13 2L3 13l10 11"/></svg></div>
<div class="arrow" style="left:1143px"><svg width="16" height="26" viewBox="0 0 16 26" fill="none" stroke="#222" stroke-width="2"><path d="M3 2l10 11L3 24"/></svg></div>
<div class="btn" style="left:517px;top:3420px;width:175px;height:43px">VIEW ALL IMAGES</div>

<!-- call to action -->
<div class="photo cta-photo" role="img" aria-label="Blue-tinted city skyline backdrop"></div>
<h2 class="abs cta-title" style="top:3570px">FLAT ROOF INSTALLATION ROOF REPAIR</h2>
<h2 class="abs cta-title" style="top:3618px">STORM DAMAGE INSURANCE SPECIALISTS</h2>
<p class="abs cta-copy">Sign up to receive maintenance reminders and hear about our latest projects.</p>
<div class="abs signup">
  <svg width="24" height="18" viewBox="0 0 24 18" fill="none" stroke="#333" stroke-width="1.6"><rect x="1" y="1" width="22" height="16"/><path d="M1 1l11 9 11-9"/></svg>
  Email Id
</div>
<div class="btn" style="left:829px;top:3753px;width:108px;height:40px">SIGN UP</div>

<!-- footer -->
<div class="abs footer"></div>
<div class="brand brand-foot"><span class="brand-mark"></span>Brevett NY Roofing</div>

<div class="fhead" style="left:425px;width:193px">CONTACT US</div>
<div class="fitem" style="left:425px;top:3970px"><span class="ic"><svg width="10" height="12" viewBox="0 0 10 12"><path d="M5 0a4 4 0 0 1 4 4c0 3-4 8-4 8S1 7 1 4a4 4 0 0 1 4-4z" fill="#171717"/></svg></span><span>48 Harbor Lane,<br>Queens NY 11101</span></div>
<div class="fitem" style="left:425px;top:4020px"><span class="ic"><svg width="12" height="12" viewBox="0 0 24 24"><path d="M5 3h4l2 5-2.5 1.5a11 11 0 0 0 6 6L16 13l5 2v4a2 2 0 0 1-2 2A17 17 0 0 1 3 5a2 2 0 0 1 2-2z" fill="#171717"/></svg></span><span>Call Us<br>555-014-2290</span></div>
<div class="fitem" style="left:425px;top:4072px"><span class="ic"><svg width="12" height="10" viewBox="0 0 12 10"><rect width="12" height="10" fill="#171717"/><path d="M0 0l6 5 6-5" stroke="#fff" fill="none"/></svg></span><span>E mail Us<br>info@brvtroofing.example</span></div>

<div class="fhead" style="left:746px;width:108px">MENU</div>
<div class="fmenu">HOME<br>CONTACT US<br>PHOTO GALLERY<br>SERVICES<br>ABOUT US</div>

<div class="fhead" style="left:960px;width:108px">FOLLOW US</div>
<div class="fitem" style="left:960px;top:3978px"><span class="ic"></span><span>Like us on<br>FRIENDWALL</span></div>
<div class="fitem" style="left:960px;top:4028px"><span class="ic"></span><span>Follow us on<br>WORKLINE</span></div>
<div class="fitem" style="left:960px;top:4080px"><span class="ic"></span><span>Follow us on<br>SNAPGRID</span></div>

<div class="fline"></div>
<div class="copy">Copyright © 2024 All Rights Reserved</div>

</body>
</html>
```